Business Card Design for Training Business

Clear Path Coaching is a new business that delivers training and other services with a focus on topics related to mental health and wellbeing, for example, Wellmind Response Course, Resilience etc. We have a strong focus on evidence-based psychology and neuroscience. I have a logo which I will upload with the brief, so please consider colours that work well with the logo.
Target Market(s)
Adults, workplaces (particularly government and not-for-profits)
Industry/Entity Type
Business
Contact Information for Business Card
Head Strong TrainingSamantha SellwoodDirector0438 770 850sam@headstrongtraining.com.auwww.headstrongtraining.com.au

```html
<!DOCTYPE html>
<html lang="en">
<head>
<meta charset="utf-8">
<title>Clear Path Coaching – Business Card</title>
<link rel="stylesheet" href="https://fonts.googleapis.com/css2?family=Arimo:wght@400&display=swap">
<style>
  :root {
    --backdrop: #9b9b9b;
    --card: #f4f4f4;
    --teal: #1fb3bf;
    --ink: #4a3d39;
    --brand-ink: #6b5f5b;
  }
  * { margin: 0; padding: 0; box-sizing: border-box; }
  html, body {
    width: 1200px;
    height: 965px;
    overflow: hidden;
    background: var(--backdrop);
    font-family: "Arimo", Arial, sans-serif;
  }
  .canvas {
    position: relative;
    width: 1200px;
    height: 965px;
  }
  .card {
    position: absolute;
    left: 255px;
    top: 287px;
    width: 690px;
    height: 391px;
    background: var(--card);
  }
  .brand {
    position: absolute;
    left: 0;
    top: 119px;
    width: 400px;
    text-align: center;
  }
  .brand-mark {
    display: block;
    margin: 0 auto;
  }
  .brand-name {
    margin-top: 28px;
    font-size: 19px;
    letter-spacing: 2px;
    text-transform: uppercase;
    color: var(--brand-ink);
    white-space: nowrap;
  }
  .person {
    position: absolute;
    left: 371px;
    top: 131px;
  }
  .person-name {
    font-size: 21px;
    line-height: 26px;
    color: var(--teal);
  }
  .person-role {
    font-size: 15.5px;
    line-height: 20px;
    color: var(--ink);
  }
  .contacts {
    list-style: none;
    margin-top: 29px;
  }
  .contact {
    display: flex;
    align-items: center;
    height: 19.5px;
    font-size: 15.5px;
    color: var(--ink);
    white-space: nowrap;
  }
  .contact-icon {
    width: 15px;
    height: 15px;
    margin-right: 11px;
    flex: none;
  }
</style>
</head>
<body>
<main class="canvas">
  <section class="card">
    <div class="brand">
      <svg class="brand-mark" width="92" height="92" viewBox="0 0 92 92" aria-hidden="true">
        <circle cx="46" cy="46" r="45" fill="var(--teal)"/>
      </svg>
      <p class="brand-name">Clear Path Coaching</p>
    </div>

    <div class="person">
      <h1 class="person-name">Rebecca Tanfield</h1>
      <p class="person-role">Director</p>

      <ul class="contacts">
        <li class="contact">
          <svg class="contact-icon" viewBox="0 0 16 16" aria-hidden="true">
            <path d="M3.2 1.2l2.3-.2 1.4 3.4-1.6 1.3c.8 1.8 2.3 3.3 4.1 4.1l1.3-1.6 3.4 1.4-.2 2.3c-.1.9-.9 1.6-1.8 1.5C6.3 13 3 9.7 1.7 4.9 1.6 4 2.3 1.3 3.2 1.2z" fill="var(--teal)"/>
          </svg>
          <span>0491 362 517</span>
        </li>
        <li class="contact">
          <svg class="contact-icon" viewBox="0 0 16 16" aria-hidden="true">
            <rect x="0.5" y="3" width="15" height="10" fill="var(--teal)"/>
            <path d="M1 3.6l7 5 7-5M1 12.5l5-4.3M15 12.5l-5-4.3" fill="none" stroke="var(--card)" stroke-width="1.2"/>
          </svg>
          <span>bec@clearpathcoaching.example.au</span>
        </li>
        <li class="contact">
          <svg class="contact-icon" viewBox="0 0 16 16" aria-hidden="true">
            <g fill="none" stroke="var(--teal)" stroke-width="1.2">
              <circle cx="8" cy="8" r="7"/>
              <ellipse cx="8" cy="8" rx="3" ry="7"/>
              <path d="M1 8h14M2 4.5h12M2 11.5h12M8 1v14"/>
            </g>
          </svg>
          <span>www.clearpathcoaching.example.au</span>
        </li>
      </ul>
    </div>
  </section>
</main>
</body>
</html>
```